Redesign and move to Wordpress for corvandel.com

Our website needs a redesign and at the same time we are moving it to Wordpress. Please help us with a new digital professional look and feel.

We are an Australian Software Engineering company specialising in advanced software development using in A.I., PLatform Engineering, Integration and Cloud. See the current corvandel.com for more information about us.

```html
<!DOCTYPE html>
<html lang="en">
<head>
<meta charset="utf-8">
<title>Corvandel — Reliable Smart Software Engineering</title>
<link href="https://fonts.googleapis.com/css2?family=Audiowide&family=Montserrat:wght@400;500;600;700&family=Poppins:wght@300;400&display=swap" rel="stylesheet">
<style>
:root{
  --navy:#0e1a36;
  --blue:#1a64a3;
  --blue-dark:#16528a;
  --teal:#4fc7b8;
  --light:#f4f4f4;
  --ink:#1d1d1d;
  --text:#444;
  --white:#fff;
}
*{margin:0;padding:0;box-sizing:border-box}
html,body{width:1200px;height:4804px;overflow:hidden}
body{font-family:'Montserrat',sans-serif;color:var(--text);background:var(--white);position:relative}
.display{font-family:'Audiowide',sans-serif;color:var(--ink);font-weight:400}
a{color:inherit;text-decoration:none}

/* header + hero */
.hero{position:absolute;left:0;top:0;width:1200px;height:900px;overflow:hidden;
  background:linear-gradient(100deg,#0c1630 0%,#12224a 45%,#2a3d66 70%,#5a6a86 100%)}
.hero-photo{position:absolute;right:0;top:127px;width:720px;height:700px;
  background:radial-gradient(ellipse at 60% 45%,rgba(210,170,110,.35),rgba(20,35,70,0) 65%)}
.site-header{position:absolute;top:0;left:0;width:1200px;height:127px;background:rgba(10,18,38,.75);z-index:2}
.brand{position:absolute;left:67px;top:42px;display:flex;align-items:center;gap:14px;color:var(--white);font-family:'Audiowide',sans-serif;font-size:30px}
.brand-mark{width:40px;height:40px;border:3px solid var(--white)}
.nav{position:absolute;top:54px;left:567px;font-size:13px;font-weight:500;color:var(--white)}
.nav a{position:absolute;white-space:nowrap}
.nav .active{color:var(--teal);border-bottom:2px solid var(--teal);padding-bottom:10px}
.nav-cta{position:absolute;left:950px;top:39px;width:136px;height:45px;background:var(--blue);color:var(--white);font-size:13px;font-weight:500;display:flex;align-items:center;justify-content:center}
.search{position:absolute;left:1112px;top:50px}
.hero-title{position:absolute;left:40px;top:230px;width:630px;text-align:center;color:var(--white);font-family:'Audiowide',sans-serif;font-weight:400;font-size:54px;line-height:69px;letter-spacing:1px}
.btn{display:flex;align-items:center;justify-content:center;gap:14px;color:var(--white);font-weight:700;font-size:17px;position:absolute}
.btn-teal{background:var(--teal);left:244px;top:496px;width:213px;height:60px}
.hero-wave{position:absolute;left:0;top:760px;z-index:1}

/* about */
.about{position:absolute;left:0;top:900px;width:1200px;height:621px;background:var(--light);text-align:center}
.section-mark{width:50px;height:50px;border:4px solid var(--blue);position:absolute;left:575px}
.section-mark::after{content:"";position:absolute;right:-12px;top:-12px;width:20px;height:20px;background:var(--teal)}
.section-title{position:absolute;left:0;width:1200px;text-align:center;font-size:46px}
.about .welcome{position:absolute;top:174px;width:1200px;color:#1b6fb3;font-size:21px;font-weight:500}
.about .copy{position:absolute;top:228px;left:140px;width:920px;font-size:14px;line-height:27px;color:#333}
.about .copy p+p{margin-top:26px}
.btn-blue{background:var(--blue)}
.about .btn{left:494px;top:460px;width:211px;height:60px}

/* services */
.services{position:absolute;left:0;top:1521px;width:1200px;height:1138px;background:var(--white)}
.service-grid{position:absolute;left:144px;top:278px;display:grid;grid-template-columns:438px 438px;column-gap:34px;row-gap:17px}
.service-card{height:172px;background:var(--blue);position:relative;color:var(--white);border-radius:4px}
.service-icon{position:absolute;left:32px;top:41px;width:90px;height:90px;border-radius:50%;border:3px solid var(--teal);background:rgba(79,199,184,.18);display:flex;align-items:center;justify-content:center}
.service-body{position:absolute;left:147px;top:30px;width:270px}
.service-body h3{font-size:14.5px;font-weight:500;line-height:19px;text-transform:uppercase}
.service-body p{font-size:11px;line-height:18px;margin-top:4px}
.service-body a{display:inline-block;margin-top:8px;font-size:11px;text-decoration:underline}

/* blog */
.blog{position:absolute;left:0;top:2659px;width:1200px;height:793px;background:var(--light)}
.posts{position:absolute;left:71px;top:239px;display:flex;gap:35px}
.post{width:330px}
.post-image{height:210px;box-shadow:6px 6px 0 var(--teal)}
.img-servers{background:linear-gradient(90deg,#0d2a1c,#1f6a3c 30%,#0c2218 50%,#2a8a4a 70%,#0d2a1c)}
.img-screen{background:linear-gradient(135deg,#1e2e44,#c89a56 55%,#2a3a52)}
.img-report{background:linear-gradient(135deg,#cfd4dc,#f2f2f2 50%,#9aa3b0)}
.post-date{margin-top:35px;font-size:12px;font-weight:600;color:#222;display:flex;align-items:center;gap:6px}
.post h4{margin-top:12px;font-size:16px;font-weight:500;line-height:27px;color:#1b6fb3}
.post .more{display:inline-block;margin-top:8px;font-size:12px;font-weight:700;color:var(--teal);text-decoration:underline}
.blog .btn{left:500px;top:635px;width:198px;height:59px}

/* newsletter */
.newsletter{position:absolute;left:0;top:3452px;width:1200px;height:678px;background:radial-gradient(ellipse at 50% 30%,#2b3760,#1b2442 60%,#141b33);text-align:center;color:var(--white)}
.newsletter .section-mark{border-color:var(--white);top:99px}
.newsletter h2{position:absolute;top:170px;width:1200px;font-family:'Audiowide',sans-serif;font-weight:400;font-size:56px;line-height:67px;color:var(--white)}
.newsletter .lede{position:absolute;top:388px;width:1200px;font-family:'Poppins',sans-serif;font-weight:300;font-size:34px;letter-spacing:-1px}
.subscribe{position:absolute;left:304px;top:493px;width:592px;height:61px;background:var(--blue);display:flex;align-items:center;padding:0 0 0 32px}
.subscribe span{font-size:14px;font-weight:500;flex:1;text-align:left}
.subscribe b{width:164px;height:41px;margin-right:14px;background:var(--white);color:var(--blue);font-size:13px;font-weight:600;display:flex;align-items:center;justify-content:center}

/* partners */
.partners{position:absolute;left:0;top:4130px;width:1200px;height:220px;background:var(--white)}
.partner{position:absolute;top:98px;width:210px;font-size:28px;font-weight:700;color:#2a2a2a;display:flex;align-items:center;justify-content:center;gap:10px;white-space:nowrap}
.partner i{display:block;width:22px;height:22px;background:#2a2a2a;flex:none}

/* footer */
.footer-wave{position:absolute;left:0;top:4290px;z-index:1}
.footer{position:absolute;left:0;top:4330px;width:1200px;height:419px;background:var(--blue-dark);color:var(--white)}
.footer h5{position:absolute;top:157px;font-family:'Audiowide',sans-serif;font-weight:400;font-size:23px}
.footer-rule{position:absolute;top:200px;height:1px;background:rgba(255,255,255,.55)}
.links{position:absolute;top:228px;list-style:none;font-size:13px;line-height:26px}
.links li::before{content:"→";margin-right:10px}
.contact{position:absolute;left:866px;top:228px;width:260px;font-size:12.5px;line-height:17px}
.contact li{list-style:none;display:flex;gap:14px;margin-bottom:16px}
.contact i{width:26px;height:26px;border-radius:50%;background:var(--blue);border:1px solid rgba(255,255,255,.3);display:flex;align-items:center;justify-content:center;flex:none}
.copyright{position:absolute;left:0;top:4749px;width:1200px;height:55px;background:#134878;color:var(--white);font-size:11px;display:flex;align-items:center;padding-left:67px}
.social{position:absolute;right:67px;top:16px;display:flex;gap:8px}
.social i{width:24px;height:24px;background:#2d7fd0;display:block}
</style>
</head>
<body>

<section class="hero">
  <div class="hero-photo" role="img" aria-label="Photo of a software engineer working on a laptop with a glowing globe and code overlay"></div>
  <header class="site-header">
    <div class="brand"><span class="brand-mark"></span>corvandel</div>
    <nav class="nav">
      <a class="active" style="left:0">HOME</a>
      <a style="left:89px">ABOUT US</a>
      <a style="left:205px">SERVICES</a>
      <a style="left:314px">BLOG</a>
    </nav>
    <a class="nav-cta">CONTACT US</a>
    <svg class="search" width="22" height="22" viewBox="0 0 22 22" fill="none" stroke="#fff" stroke-width="2"><circle cx="9" cy="9" r="7"/><path d="M14 14l6 6"/></svg>
  </header>
  <h1 class="hero-title">Reliable Smart<br>Software<br>Engineering</h1>
  <a class="btn btn-teal">KNOW MORE
    <svg width="18" height="12" viewBox="0 0 18 12" fill="none" stroke="#fff" stroke-width="2"><path d="M1 6h15M11 1l5 5-5 5"/></svg></a>
  <svg class="hero-wave" width="1200" height="140" viewBox="0 0 1200 140">
    <polygon points="0,100 802,15 1200,50 1200,140 0,140" fill="#4fc7b8"/>
    <polygon points="0,140 802,30 1200,70 1200,140" fill="#f4f4f4"/>
  </svg>
</section>

<section class="about">
  <div class="section-mark" style="top:18px"></div>
  <h2 class="section-title display" style="top:70px">About Us</h2>
  <p class="welcome">Welcome to Corvandel!</p>
  <div class="copy">
    <p>Since our inception in 2013, we have been on a mission to make complex custom enterprise integration accessible to any organization, regardless of industry, size, or location.</p>
    <p>Our journey began with a focus on Integration Architecture, quickly moving into delivering bespoke systems integration using Northwind technologies like FlowBridge, CoreNet, SQL Engine, and LinkComm. Our commitment to excellence quickly earned us recognition, and in 2014, we became a proud Northwind Gold Partner, achieving this accolade with the creation of our first 100% native Nimbus cloud solution. We have upheld this esteemed partnership ever since.</p>
  </div>
  <a class="btn btn-blue">READ MORE
    <svg width="18" height="12" viewBox="0 0 18 12" fill="none" stroke="#fff" stroke-width="2"><path d="M1 6h15M11 1l5 5-5 5"/></svg></a>
</section>

<section class="services">
  <div class="section-mark" style="top:99px"></div>
  <h2 class="section-title display" style="top:150px">Our Services</h2>
  <div class="service-grid">
    <article class="service-card"><div class="service-icon"><svg width="46" height="46" viewBox="0 0 46 46" fill="none" stroke="#fff" stroke-width="2"><circle cx="9" cy="9" r="4"/><circle cx="23" cy="9" r="4"/><circle cx="37" cy="9" r="4"/><circle cx="9" cy="37" r="4"/><circle cx="23" cy="37" r="4"/><circle cx="37" cy="37" r="4"/><path d="M9 23h28"/></svg></div>
      <div class="service-body"><h3>Enterprise Systems Integration</h3><p>Automate your business processes internally or externally to improve data quality</p><a>READ MORE</a></div></article>
    <article class="service-card"><div class="service-icon"><svg width="46" height="46" viewBox="0 0 46 46" fill="none" stroke="#fff" stroke-width="2"><circle cx="23" cy="23" r="5"/><circle cx="8" cy="8" r="4"/><circle cx="38" cy="8" r="4"/><circle cx="8" cy="38" r="4"/><circle cx="38" cy="38" r="4"/><path d="M11 11l8 8M35 11l-8 8M11 35l8-8M35 35l-8-8"/></svg></div>
      <div class="service-body"><h3>Microservices</h3><p>Leverage Microservices Architecture to enable quick deployment, dynamically scalable service performance.</p><a>READ MORE</a></div></article>
    <article class="service-card"><div class="service-icon"><svg width="46" height="46" viewBox="0 0 46 46" fill="none" stroke="#fff" stroke-width="2"><path d="M12 30a8 8 0 0 1 1-16 11 11 0 0 1 21 2 7 7 0 0 1-1 14z"/><path d="M23 30v10M17 34v6M29 34v6"/></svg></div>
      <div class="service-body"><h3>Platform Engineering</h3><p>For organisations looking to manage the security and cost risks around their cloud infrastructure management for applications</p><a>READ MORE</a></div></article>
    <article class="service-card"><div class="service-icon"><svg width="46" height="46" viewBox="0 0 46 46" fill="none" stroke="#fff" stroke-width="2"><rect x="6" y="8" width="26" height="20" rx="3"/><path d="M12 28v7l7-7"/><rect x="18" y="18" width="22" height="16" rx="3"/></svg></div>
      <div class="service-body"><h3>Conversational AI</h3><p>Enabling legacy systems with conversational user interfaces, or simply building intelligent natural language based services.</p><a>READ MORE</a></div></article>
    <article class="service-card"><div class="service-icon"><svg width="46" height="46" viewBox="0 0 46 46" fill="none" stroke="#fff" stroke-width="2"><rect x="12" y="4" width="22" height="10"/><rect x="4" y="32" width="14" height="10"/><rect x="28" y="32" width="14" height="10"/><path d="M23 14v9M11 32v-9h24v9"/></svg></div>
      <div class="service-body"><h3>iPaaS</h3><p>Integration Platform as a Service brings the power of cloud based services to traditional systems integration.</p><a>READ MORE</a></div></article>
    <article class="service-card"><div class="service-icon"><svg width="46" height="46" viewBox="0 0 46 46" fill="none" stroke="#fff" stroke-width="2"><path d="M14 42v-8c-6-4-8-10-6-17a15 15 0 0 1 29 4l3 7h-4v6h-7v8"/><circle cx="24" cy="19" r="4"/></svg></div>
      <div class="service-body"><h3>Assistant / AI Agents</h3><p>The future of business AI are autonomous agents that specialise in your business data and processes.</p><a>READ MORE</a></div></article>
    <article class="service-card"><div class="service-icon"><svg width="46" height="46" viewBox="0 0 46 46" fill="none" stroke="#fff" stroke-width="2"><path d="M23 6a17 17 0 1 0 17 17"/><path d="M40 6v10H30"/><path d="M17 23h12M23 17v12"/></svg></div>
      <div class="service-body"><h3>Real-Time Data Stream Processing</h3><p>Being able to react to changing business conditions in a precise intelligent way</p><a>READ MORE</a></div></article>
    <article class="service-card"><div class="service-icon"><svg width="46" height="46" viewBox="0 0 46 46" fill="none" stroke="#fff" stroke-width="2"><path d="M6 40h34M12 40V28M20 40V20M28 40V24M36 40V12"/></svg></div>
      <div class="service-body"><h3>Custom Integration for Small to Medium Business</h3><p>Our expertise in platform engineering, iPaaS, building distributed systems and enterprise</p><a>READ MORE</a></div></article>
  </div>
</section>

<section class="blog">
  <div class="section-mark" style="top:80px"></div>
  <h2 class="section-title display" style="top:132px">Our Blog</h2>
  <div class="posts">
    <article class="post"><div class="post-image img-servers" role="img" aria-label="Photo of server racks in a data centre lit in green"></div>
      <p class="post-date"><svg width="12" height="12" viewBox="0 0 12 12" fill="none" stroke="#4fc7b8" stroke-width="1.5"><rect x="1" y="2" width="10" height="9"/><path d="M1 5h10"/></svg>June 24, 2024</p>
      <h4>Why most upgrade paths for FlowBridge lead to using Nimbus Logic apps</h4><a class="more">READ MORE</a></article>
    <article class="post"><div class="post-image img-screen" role="img" aria-label="Photo of a monitor showing a glowing data visualisation in a dark office"></div>
      <p class="post-date"><svg width="12" height="12" viewBox="0 0 12 12" fill="none" stroke="#4fc7b8" stroke-width="1.5"><rect x="1" y="2" width="10" height="9"/><path d="M1 5h10"/></svg>June 14, 2024</p>
      <h4>How to get visibility into your FlowBridge environment</h4><a class="more">READ MORE</a></article>
    <article class="post"><div class="post-image img-report" role="img" aria-label="Photo of a tablet displaying a security vulnerability report"></div>
      <p class="post-date"><svg width="12" height="12" viewBox="0 0 12 12" fill="none" stroke="#4fc7b8" stroke-width="1.5"><rect x="1" y="2" width="10" height="9"/><path d="M1 5h10"/></svg>June 12, 2024</p>
      <h4>Top 10 FlowBridge Server Vulnerabilities and Security Recommendations</h4><a class="more">READ MORE</a></article>
  </div>
  <a class="btn btn-blue">VIEW MORE
    <svg width="18" height="12" viewBox="0 0 18 12" fill="none" stroke="#fff" stroke-width="2"><path d="M1 6h15M11 1l5 5-5 5"/></svg></a>
</section>

<section class="newsletter" role="img" aria-label="Dark blue background with a faint technology scene">
  <div class="section-mark"></div>
  <h2>Australia's Largest<br>health charity implements<br>CORVANDEL API MSG BUS</h2>
  <p class="lede">Register to our newsletter to find out more.</p>
  <div class="subscribe"><span>Enter Your Email Address</span><b>Subscribe</b></div>
</section>

<section class="partners">
  <div class="partner" style="left:150px">Halvern</div>
  <div class="partner" style="left:365px"><i></i>Northwind</div>
  <div class="partner" style="left:590px">Tallrock</div>
  <div class="partner" style="left:815px"><i style="border-radius:50%"></i>brightfund</div>
</section>

<svg class="footer-wave" width="1200" height="150" viewBox="0 0 1200 150">
  <polygon points="0,0 784,130 1200,40 1200,150 0,150" fill="#4fc7b8"/>
  <polygon points="0,30 784,150 1200,70 1200,150 0,150" fill="#16528a"/>
</svg>

<footer class="footer">
  <h5 style="left:99px">Quick Links</h5>
  <h5 style="left:347px">Our Services</h5>
  <h5 style="left:866px">Contact Us</h5>
  <div class="footer-rule" style="left:80px;width:740px"></div>
  <div class="footer-rule" style="left:850px;width:285px"></div>
  <ul class="links" style="left:95px"><li>Home</li><li>About Us</li><li>Services</li><li>Blog</li><li>Contact Us</li></ul>
  <ul class="links" style="left:345px"><li>Enterprise Systems Integration</li><li>Microservices</li><li>Platform Engineering</li><li>Conversation A.I.</li><li>iPaaS</li></ul>
  <ul class="links" style="left:622px"><li>A.I. Agents</li><li>Real-time Data Stream<br>&nbsp;&nbsp;&nbsp;&nbsp;&nbsp;Processing</li><li>Streamly</li><li>Technology Expertise</li></ul>
  <ul class="contact">
    <li><i><svg width="12" height="12" viewBox="0 0 12 12" fill="#fff"><path d="M2 1h3l1 3-2 1a7 7 0 0 0 3 3l1-2 3 1v3c-6 1-10-4-9-9z"/></svg></i><span>CALL US<br>1800 555 019</span></li>
    <li><i><svg width="12" height="10" viewBox="0 0 12 10" fill="none" stroke="#fff" stroke-width="1.4"><rect x="1" y="1" width="10" height="8"/><path d="M1 1l5 4 5-4"/></svg></i><span>EMAIL US<br>info@corvandel.com</span></li>
    <li><i><svg width="10" height="13" viewBox="0 0 10 13" fill="#fff"><path d="M5 0a5 5 0 0 1 5 5c0 3-5 8-5 8S0 8 0 5a5 5 0 0 1 5-5z"/><circle cx="5" cy="5" r="2" fill="#16528a"/></svg></i><span>Suite 12, 48 Harbour Lane<br>Melbourne, VIC , 3004</span></li>
  </ul>
</footer>

<div class="copyright">Copyright © 2025 All Rights Reserved By corvandel
  <div class="social"><i></i><i></i><i></i></div>
</div>

</body>
</html>
```